Bork Ventures, Inc. Website redesign

Revamp the website, it is old and outdated. www.borkventuresinc.example

Target Market(s)

Information Technology Consulting and Staffing

Coding

Coded - Design and coding required

Number of Pages Required

5+ page

Colors

Designer to choose colors to be used in the design.

Requirements
Must have
• Outlined text boxes just like from the Tolvane.example site. A clean look

```html
<!DOCTYPE html>
<html lang="en">
<head>
<meta charset="utf-8">
<title>Bork Ventures, Inc. — Website Redesign</title>
<link rel="stylesheet" href="https://fonts.googleapis.com/css2?family=Oswald:wght@400;600;700&family=Open+Sans:wght@400;600;700&family=Playfair+Display:wght@400;700&display=swap">
<style>
:root{
  --crimson:#a5192f;
  --crimson-dark:#7d1022;
  --ink:#111114;
  --charcoal:#1d1d22;
  --mist:#ececec;
  --line:#d2d2d2;
  --paper:#ffffff;
  --photo-server:linear-gradient(135deg,#1a2230 0%,#39485e 45%,#0d1118 100%);
  --photo-office:linear-gradient(160deg,#cfd6de 0%,#8d9aa8 60%,#5e6b78 100%);
  --photo-tech:linear-gradient(135deg,#0b1f4a 0%,#2b5fb0 50%,#9cc3f0 100%);
}
*{box-sizing:border-box;margin:0;padding:0}
html,body{width:1200px;height:3332px;overflow:hidden}
body{position:relative;background:var(--paper);font-family:"Open Sans",Arial,sans-serif;color:var(--ink)}
.abs{position:absolute}
.photo{position:absolute}

.board-top{position:absolute;left:0;top:0;width:1200px;height:520px;background:var(--ink)}
.board-top svg{position:absolute;left:0;top:0}

.brand{display:flex;align-items:center;gap:14px;color:var(--paper)}
.brand-name{font-family:"Oswald",sans-serif;font-weight:700;font-size:36px;letter-spacing:3px}
.brand-dot{width:16px;height:16px;background:var(--crimson);border-radius:50%}

.section-title{font-family:"Oswald",sans-serif;font-weight:600;text-align:center;letter-spacing:1px}
.btn{display:inline-block;background:var(--crimson);color:var(--paper);font-family:"Oswald",sans-serif;font-size:9px;padding:5px 12px;letter-spacing:1px}
.para{font-size:6.5px;line-height:10px;color:#555}
.bar{height:5px;background:var(--line);margin-bottom:5px}

.desk{position:absolute;left:248px;top:820px;width:652px;height:1480px;background:var(--paper);box-shadow:0 0 14px rgba(0,0,0,.18);overflow:hidden}
.nav{position:absolute;left:0;top:0;width:100%;height:28px;display:flex;align-items:center;justify-content:space-between;padding:0 26px;border-bottom:1px solid var(--line)}
.nav-brand{font-family:"Oswald",sans-serif;font-weight:700;font-size:12px;letter-spacing:1px;color:var(--crimson)}
.nav-links{display:flex;gap:16px;font-size:7px;color:#444}
.nav-links .on{color:var(--crimson);font-weight:700}
.hero{position:absolute;left:0;top:28px;width:100%;height:192px;background:var(--photo-server)}
.hero-copy{position:absolute;left:300px;top:66px;color:var(--paper)}
.hero-kicker{font-family:"Oswald",sans-serif;font-size:13px;letter-spacing:1px}
.hero-big{font-family:"Oswald",sans-serif;font-weight:700;font-size:44px;line-height:46px;color:var(--crimson);letter-spacing:1px}
.hero-sub{font-family:"Oswald",sans-serif;font-size:10px;letter-spacing:1px;margin:2px 0 10px}

.services{position:absolute;left:0;top:236px;width:100%;height:180px}
.services .section-title{font-size:18px}
.svc-row{position:absolute;left:36px;top:40px;width:580px;display:flex;justify-content:space-between}
.svc{width:96px;text-align:center}
.svc-ring{width:46px;height:46px;border:2px solid var(--crimson);border-radius:50%;margin:0 auto 8px;display:flex;align-items:center;justify-content:center;background:var(--paper)}
.svc.on .svc-ring{background:var(--crimson)}
.svc-name{font-family:"Oswald",sans-serif;font-size:8px;letter-spacing:.5px;margin-bottom:4px}

.about{position:absolute;left:0;top:432px;width:100%;height:196px;background:var(--mist)}
.about-frame{position:absolute;left:80px;top:14px;width:180px;height:168px;border:3px solid var(--crimson)}
.about-copy{position:absolute;left:300px;top:34px;width:300px}
.kicker{font-family:"Oswald",sans-serif;font-size:7px;color:var(--crimson);letter-spacing:1px}
.head-lg{font-family:"Oswald",sans-serif;font-weight:600;font-size:20px;letter-spacing:1px;margin:2px 0 8px}

.leaders{position:absolute;left:0;top:646px;width:100%;height:160px}
.leaders .section-title{font-size:16px}
.leader-ring{position:absolute;left:296px;top:30px;width:60px;height:60px;border-radius:50%;border:3px solid var(--crimson);background:var(--photo-office)}
.leader-name{position:absolute;left:0;top:98px;width:100%;text-align:center;font-size:7px;font-weight:700}
.leader-note{position:absolute;left:176px;top:112px;width:300px;text-align:center}
.arrow{position:absolute;top:52px;font-size:16px;color:#bbb}

.path{position:absolute;left:0;top:824px;width:100%;height:216px;background:var(--photo-tech)}
.path-box{position:absolute;left:26px;top:844px;width:200px;height:190px;background:var(--crimson);padding:18px 16px;color:var(--paper)}
.path-box .kicker{color:#f3c4cc}
.path-box .head-lg{font-size:15px;line-height:18px}
.path-box .para{color:#f6dde2}

.news{position:absolute;left:0;top:1060px;width:100%;height:250px}
.news .section-title{font-size:16px}
.news-row{position:absolute;left:36px;top:36px;width:580px;display:flex;justify-content:space-between}
.card{width:180px}
.card-photo{width:180px;height:92px;margin-bottom:8px}
.card-title{font-size:7px;font-weight:700;line-height:10px;margin-bottom:4px}

.footer{position:absolute;left:0;top:1326px;width:100%;height:154px;background:var(--charcoal);color:#ccc}
.footer-strip{position:absolute;left:0;top:0;width:100%;height:6px;background:var(--crimson)}
.foot-brand{position:absolute;left:40px;top:26px;font-family:"Oswald",sans-serif;font-weight:700;font-size:14px;letter-spacing:1px;color:var(--paper)}
.foot-col{position:absolute;top:26px;width:110px;font-size:6.5px;line-height:12px}
.foot-col h4{font-family:"Oswald",sans-serif;font-size:8px;color:var(--paper);font-weight:600;margin-bottom:4px;letter-spacing:1px}
.dot-row{display:flex;gap:6px;margin-top:8px}
.dot-row span{width:12px;height:12px;border-radius:50%;background:var(--crimson)}
.foot-base{position:absolute;left:0;bottom:0;width:100%;height:18px;background:var(--ink);font-size:6px;color:#888;text-align:center;line-height:18px}

.mob{position:absolute;left:912px;top:800px;width:192px;height:2360px;background:var(--paper);box-shadow:0 0 14px rgba(0,0,0,.18);overflow:hidden}
.m-head{position:absolute;left:0;top:0;width:100%;height:40px;display:flex;align-items:center;justify-content:space-between;padding:0 12px;border-bottom:1px solid var(--line)}
.m-burger{width:14px;height:10px;border-top:2px solid var(--ink);border-bottom:2px solid var(--ink);position:relative}
.m-burger::after{content:"";position:absolute;left:0;top:2px;width:14px;height:2px;background:var(--ink)}
.m-hero{position:absolute;left:0;top:40px;width:100%;height:170px;background:var(--photo-server)}
.m-services{position:absolute;left:0;top:210px;width:100%;height:180px;background:var(--crimson);color:var(--paper);text-align:center;padding-top:14px}
.m-services .section-title{font-size:13px}
.m-svc{width:36px;height:36px;border-radius:50%;background:var(--paper);margin:12px auto 4px}
.m-about{position:absolute;left:0;top:390px;width:100%;height:330px;background:var(--mist)}
.m-leaders{position:absolute;left:0;top:720px;width:100%;height:150px;text-align:center;padding-top:14px}
.m-path{position:absolute;left:0;top:870px;width:100%;height:310px}
.m-path-box{position:absolute;left:12px;top:40px;width:168px;height:260px;background:var(--crimson);padding:16px 12px}
.m-news{position:absolute;left:0;top:1180px;width:100%;height:700px;text-align:center;padding-top:14px}
.m-card{margin:14px 12px 0;text-align:left}
.m-card .card-photo{width:168px;height:110px}
.m-footer{position:absolute;left:0;top:1900px;width:100%;height:460px;background:var(--charcoal);color:#ccc;padding:22px 14px}

.desk-label{position:absolute;left:280px;top:716px;font-family:"Playfair Display",serif;font-size:56px;color:var(--ink)}
.thanks{position:absolute;left:200px;top:2400px;font-family:"Oswald",sans-serif;font-weight:700;font-size:112px;line-height:124px;color:var(--crimson);letter-spacing:4px}
.closing-brand{position:absolute;left:210px;top:2690px}
.closing-brand .brand{color:var(--ink)}
</style>
</head>
<body>

<div class="board-top">
  <svg width="1200" height="520" viewBox="0 0 1200 520" aria-hidden="true">
    <polygon points="0,520 1200,300 1200,520" fill="#ffffff"/>
  </svg>
</div>
<div class="abs" style="left:400px;top:40px">
  <div class="brand"><span class="brand-name">BORK VENTURES</span><span class="brand-dot"></span></div>
</div>

<div class="abs" style="left:250px;top:150px;width:620px;height:380px;background:var(--paper);overflow:hidden;box-shadow:0 0 18px rgba(0,0,0,.4)">
  <div class="nav" style="height:26px"><span class="nav-brand">BORK VENTURES</span><span class="nav-links"><span class="on">Home</span><span>About</span><span>Services</span><span>People</span><span>News</span><span>Contact</span></span></div>
  <div class="photo" role="img" aria-label="Server room network cables" style="left:0;top:26px;width:620px;height:290px;background:var(--photo-server)"></div>
  <div class="hero-copy" style="left:300px;top:90px">
    <div class="hero-kicker">BRINGING THOUGHT</div>
    <div class="hero-big">LEADERSHIP</div>
    <div class="hero-sub">&amp; QUALITY TO EVERY PROJECT</div>
    <span class="btn">CONTACT US</span>
  </div>
  <div class="section-title" style="position:absolute;left:0;top:330px;width:100%;font-size:18px">SERVICES</div>
  <div style="position:absolute;left:290px;top:360px;width:40px;height:4px;background:var(--crimson)"></div>
</div>

<div class="abs" style="left:902px;top:190px;width:170px;height:330px;background:var(--paper);overflow:hidden;box-shadow:0 0 18px rgba(0,0,0,.4)">
  <div class="m-head" style="height:28px;padding:0 8px"><span class="nav-brand" style="font-size:9px">BORK VENTURES</span><span class="m-burger"></span></div>
  <div class="photo" role="img" aria-label="Server room network cables" style="left:0;top:28px;width:170px;height:160px;background:var(--photo-server)"></div>
  <div class="abs" style="left:12px;top:60px;color:#fff">
    <div class="hero-kicker" style="font-size:9px">BRINGING THOUGHT</div>
    <div class="hero-big" style="font-size:24px;line-height:26px">LEADERSHIP</div>
    <div class="hero-sub" style="font-size:7px">&amp; QUALITY TO EVERY PROJECT</div>
    <span class="btn">CONTACT US</span>
  </div>
  <div class="abs" style="left:0;top:188px;width:170px;height:142px;background:var(--crimson);color:#fff;text-align:center;padding-top:12px">
    <div class="section-title" style="font-size:12px">SERVICES</div>
    <div class="m-svc"></div>
    <div class="svc-name">IT CONSULTING</div>
  </div>
</div>

<div class="desk-label">Desktop</div>

<div class="desk">
  <div class="nav"><span class="nav-brand">BORK VENTURES</span><span class="nav-links"><span class="on">Home</span><span>About</span><span>Services</span><span>People</span><span>News</span><span>Contact</span></span></div>
  <div class="hero" role="img" aria-label="Server room network cables"></div>
  <div class="hero-copy">
    <div class="hero-kicker">BRINGING THOUGHT</div>
    <div class="hero-big">LEADERSHIP</div>
    <div class="hero-sub">&amp; QUALITY TO EVERY PROJECT</div>
    <span class="btn">CONTACT US</span>
  </div>

  <div class="services">
    <div class="section-title">SERVICES</div>
    <div class="svc-row">
      <div class="svc"><div class="svc-ring"><svg width="20" height="20" viewBox="0 0 20 20"><rect x="2" y="4" width="16" height="10" fill="none" stroke="#a5192f" stroke-width="2"/><rect x="7" y="15" width="6" height="2" fill="#a5192f"/></svg></div><div class="svc-name">IT CONSULTING</div><div class="para">Expert guidance for your systems.</div></div>
      <div class="svc"><div class="svc-ring"><svg width="20" height="20" viewBox="0 0 20 20"><circle cx="10" cy="7" r="4" fill="none" stroke="#a5192f" stroke-width="2"/><path d="M3 18c1-5 13-5 14 0" fill="none" stroke="#a5192f" stroke-width="2"/></svg></div><div class="svc-name">IT STAFFING</div><div class="para">Skilled people when you need them.</div></div>
      <div class="svc on"><div class="svc-ring"><svg width="20" height="20" viewBox="0 0 20 20"><path d="M4 10l4 4 8-8" fill="none" stroke="#fff" stroke-width="2.5"/></svg></div><div class="svc-name">PROJECT DELIVERY</div><div class="para">Plans carried through to results.</div></div>
      <div class="svc"><div class="svc-ring"><svg width="20" height="20" viewBox="0 0 20 20"><path d="M7 5l-5 5 5 5M13 5l5 5-5 5" fill="none" stroke="#a5192f" stroke-width="2"/></svg></div><div class="svc-name">DEVELOPMENT</div><div class="para">Custom code built to last.</div></div>
      <div class="svc"><div class="svc-ring"><svg width="20" height="20" viewBox="0 0 20 20"><path d="M10 2l7 3v5c0 4-3 7-7 8-4-1-7-4-7-8V5z" fill="none" stroke="#a5192f" stroke-width="2"/></svg></div><div class="svc-name">SECURITY</div><div class="para">Protection for data and networks.</div></div>
    </div>
  </div>

  <div class="about">
    <div class="about-frame"></div>
    <div class="photo" role="img" aria-label="Consultant standing in a data center" style="left:94px;top:28px;width:180px;height:168px;background:var(--photo-office)"></div>
    <div class="about-copy">
      <div class="kicker">ABOUT US</div>
      <div class="head-lg">BORK VENTURES</div>
      <p class="para">Bork Ventures delivers technology consulting and staffing to organizations of every size. Our team pairs deep technical skill with a steady focus on mission, integrity and results for each client we serve.</p>
      <div style="margin-top:10px"><span class="btn">READ MORE</span></div>
    </div>
  </div>

  <div class="leaders">
    <div class="section-title">OUR LEADERS</div>
    <div class="arrow" style="left:120px">‹</div>
    <div class="leader-ring" role="img" aria-label="Portrait of company leader"></div>
    <div class="arrow" style="left:524px">›</div>
    <div class="leader-name">Dana Holt — Chief Executive Officer</div>
    <p class="para leader-note">Leading our teams with vision and care for every client partnership.</p>
  </div>

  <div class="path" role="img" aria-label="Abstract blue technology network"></div>
  <div class="path-box">
    <div class="kicker">OUR STRATEGY</div>
    <div class="head-lg">YOUR PATH TO SUCCESS</div>
    <p class="para">We study your goals, design a clear plan and place the right people to carry it out. Each step is measured so progress stays visible and every outcome is earned.</p>
    <div style="margin-top:12px"><span class="btn" style="background:#fff;color:var(--crimson)">LEARN MORE</span></div>
  </div>

  <div class="news">
    <div class="section-title">LATEST IT NEWS</div>
    <div class="news-row">
      <div class="card"><div class="card-photo" role="img" aria-label="Technician working with hardware" style="background:var(--photo-tech)"></div><div class="card-title">New cloud tools reshape how teams plan work</div><div class="bar"></div><div class="bar" style="width:70%"></div><span class="btn">READ MORE</span></div>
      <div class="card"><div class="card-photo" role="img" aria-label="Team meeting at laptops" style="background:var(--photo-office)"></div><div class="card-title">Hiring trends for skilled IT staff this year</div><div class="bar"></div><div class="bar" style="width:70%"></div><span class="btn">READ MORE</span></div>
      <div class="card"><div class="card-photo" role="img" aria-label="Developer at a computer" style="background:var(--photo-tech)"></div><div class="card-title">Security basics every office should follow</div><div class="bar"></div><div class="bar" style="width:70%"></div><span class="btn">READ MORE</span></div>
    </div>
  </div>

  <div class="footer">
    <div class="footer-strip"></div>
    <div class="foot-brand">BORK VENTURES</div>
    <div class="foot-col" style="left:230px"><h4>QUICK LINKS</h4>Home<br>About<br>Services<br>Contact</div>
    <div class="foot-col" style="left:360px"><h4>SERVICES</h4>Consulting<br>Staffing<br>Development<br>Security</div>
    <div class="foot-col" style="left:490px;width:140px"><h4>CONTACT US</h4>www.borkventuresinc.example<div class="dot-row"><span></span><span></span><span></span></div></div>
    <div class="foot-base">© Bork Ventures, Inc. All rights reserved.</div>
  </div>
</div>

<div class="mob">
  <div class="m-head"><span class="nav-brand" style="font-size:10px">BORK VENTURES</span><span class="m-burger"></span></div>
  <div class="m-hero" role="img" aria-label="Server room network cables"></div>
  <div class="abs" style="left:14px;top:80px;color:#fff">
    <div class="hero-kicker" style="font-size:9px">BRINGING THOUGHT</div>
    <div class="hero-big" style="font-size:26px;line-height:28px">LEADERSHIP</div>
    <div class="hero-sub" style="font-size:7px">&amp; QUALITY TO EVERY PROJECT</div>
    <span class="btn">CONTACT US</span>
  </div>
  <div class="m-services">
    <div class="section-title">SERVICES</div>
    <div class="m-svc"></div><div class="svc-name">IT CONSULTING</div>
    <div class="para" style="color:#f6dde2;padding:0 20px">Expert guidance for your systems.</div>
    <div class="m-svc"></div>
  </div>
  <div class="m-about">
    <div class="photo" role="img" aria-label="Consultant standing in a data center" style="left:24px;top:20px;width:144px;height:140px;background:var(--photo-office);border:3px solid var(--crimson)"></div>
    <div class="abs" style="left:14px;top:180px;width:164px;text-align:center">
      <div class="kicker">ABOUT US</div>
      <div class="head-lg" style="font-size:14px">BORK VENTURES</div>
      <p class="para">Technology consulting and staffing guided by mission, integrity and results.</p>
      <div style="margin-top:8px"><span class="btn">READ MORE</span></div>
    </div>
  </div>
  <div class="m-leaders">
    <div class="section-title" style="font-size:12px">OUR LEADERS</div>
    <div role="img" aria-label="Portrait of company leader" style="width:50px;height:50px;border-radius:50%;border:3px solid var(--crimson);background:var(--photo-office);margin:10px auto 6px"></div>
    <div style="font-size:7px;font-weight:700">Dana Holt — Chief Executive Officer</div>
  </div>
  <div class="m-path">
    <div class="abs" style="left:0;top:10px;width:100%;text-align:center"><div class="kicker">OUR STRATEGY</div><div class="head-lg" style="font-size:12px">YOUR PATH TO SUCCESS</div></div>
    <div class="m-path-box">
      <p class="para" style="color:#f6dde2">We study your goals, design a clear plan and place the right people to carry it out. Each step is measured so progress stays visible and every outcome is earned.</p>
      <div style="margin-top:12px"><span class="btn" style="background:#fff;color:var(--crimson)">LEARN MORE</span></div>
    </div>
  </div>
  <div class="m-news">
    <div class="section-title" style="font-size:12px">LATEST IT NEWS</div>
    <div class="m-card"><div class="card-photo" role="img" aria-label="Technician working with hardware" style="background:var(--photo-tech)"></div><div class="card-title">New cloud tools reshape how teams plan work</div><div class="bar"></div><span class="btn">READ MORE</span></div>
    <div class="m-card"><div class="card-photo" role="img" aria-label="Network cables in a rack" style="background:var(--photo-server)"></div><div class="card-title">Hiring trends for skilled IT staff this year</div><div class="bar"></div><span class="btn">READ MORE</span></div>
    <div class="m-card"><div class="card-photo" role="img" aria-label="Developer at a computer" style="background:var(--photo-tech)"></div><div class="card-title">Security basics every office should follow</div><div class="bar"></div><span class="btn">READ MORE</span></div>
  </div>
  <div class="m-footer">
    <div class="footer-strip"></div>
    <div class="nav-brand" style="color:#fff;font-size:13px">BORK VENTURES</div>
    <div class="foot-col" style="position:static;margin-top:26px"><h4>QUICK LINKS</h4>Home<br>About<br>Services<br>Contact</div>
    <div class="foot-col" style="position:static;margin-top:20px"><h4>SERVICES</h4>Consulting<br>Staffing<br>Development<br>Security</div>
    <div class="foot-col" style="position:static;margin-top:20px;width:160px"><h4>CONTACT US</h4>www.borkventuresinc.example<div class="dot-row"><span></span><span></span><span></span></div></div>
    <div class="foot-base" style="background:var(--crimson);color:#fff">© Bork Ventures, Inc.</div>
  </div>
</div>

<div class="thanks">THANK<br>YOU</div>
<div class="closing-brand">
  <div class="brand"><span class="brand-name">BORK VENTURES</span><span class="brand-dot"></span></div>
</div>

</body>
</html>
```